German Headhunter/ HR Consultancy needs Business Cards Design

We need a business Card Design for our Company in Stuttgart. We are specialized as Headhunter/ HR Consultancy in Placement of specialist and managers in permanent employment. Please refer to our business logo.

```html
<!DOCTYPE html>
<html lang="de">
<head>
<meta charset="utf-8">
<title>Nordlicht Personalberatung – Visitenkarte</title>
<link href="https://fonts.googleapis.com/css2?family=Montserrat:wght@500;600;700&family=Arimo:wght@400;700&display=swap" rel="stylesheet">
<style>
  :root {
    --brand-blue: #3a54a4;
    --brand-blue-light: #5b72bf;
    --paper: #ffffff;
    --tint: #e6e9f4;
    --backdrop: #e9e9e7;
    --ink-grey: #8a8a8a;
  }
  * { box-sizing: border-box; margin: 0; padding: 0; }
  html, body { width: 1200px; height: 802px; overflow: hidden; }
  body {
    background: var(--backdrop);
    font-family: "Arimo", Arial, sans-serif;
    display: flex;
    align-items: center;
    justify-content: center;
    gap: 60px;
  }
  .card {
    position: relative;
    width: 510px;
    height: 292px;
    background: var(--brand-blue);
    color: var(--paper);
    overflow: hidden;
    box-shadow: 0 4px 14px rgba(0,0,0,0.18);
  }
  /* Front */
  .front-panel {
    position: absolute;
    inset: 0;
    width: 100%;
    height: 100%;
  }
  .front-logo {
    position: absolute;
    top: 58px;
    right: 26px;
    display: flex;
    align-items: center;
    gap: 8px;
    color: var(--brand-blue);
  }
  .logo-square {
    width: 22px;
    height: 22px;
    background: currentColor;
    flex: none;
  }
  .logo-text {
    font-family: "Montserrat", Arial, sans-serif;
    font-weight: 700;
    line-height: 1.05;
    letter-spacing: 0.02em;
  }
  .front-logo .logo-text { font-size: 17px; }
  .logo-text .logo-sub { display: block; font-size: 0.52em; letter-spacing: 0.06em; }
  .contact {
    position: absolute;
    left: 38px;
    bottom: 36px;
    font-size: 13px;
    line-height: 1.3;
  }
  .contact-name {
    font-weight: 700;
    font-size: 17px;
    letter-spacing: 0.04em;
    text-transform: uppercase;
  }
  .contact-role { font-size: 13px; margin-bottom: 18px; }
  .contact-address { margin-bottom: 16px; }
  .contact-list { list-style: none; }
  .contact-list li { display: flex; align-items: center; gap: 8px; }
  .contact-list svg { width: 11px; height: 11px; flex: none; }
  /* Back */
  .back-accent {
    position: absolute;
    top: 26px;
    right: 34px;
    width: 170px;
    height: 170px;
    border-radius: 18px;
    background: var(--brand-blue-light);
    opacity: 0.55;
  }
  .back-logo {
    position: absolute;
    left: 40px;
    bottom: 48px;
    display: flex;
    align-items: center;
    gap: 10px;
  }
  .back-logo .logo-square { width: 28px; height: 28px; }
  .back-logo .logo-text { font-size: 30px; }
</style>
</head>
<body>
  <section class="card card-front" aria-label="Vorderseite">
    <svg class="front-panel" viewBox="0 0 510 292" preserveAspectRatio="none" aria-hidden="true">
      <polygon points="270,0 510,0 510,292 430,292" fill="var(--paper)"/>
      <rect x="360" y="20" width="120" height="140" rx="10" fill="var(--tint)"/>
    </svg>
    <div class="front-logo">
      <span class="logo-square"></span>
      <span class="logo-text">NORDLICHT<span class="logo-sub">PERSONALBERATUNG</span></span>
    </div>
    <div class="contact">
      <p class="contact-name">Lukas Brenner</p>
      <p class="contact-role">Manager</p>
      <p class="contact-address">Your address, city<br>state, ZIP 0000</p>
      <ul class="contact-list">
        <li><svg viewBox="0 0 12 12" aria-hidden="true"><path d="M3 1l2 2-1 1.5c.6 1.4 1.6 2.4 3 3L8.5 6.5l2 2L9 10.5C5 10 2 7 1.5 3z" fill="currentColor"/></svg>123-456-2100</li>
        <li><svg viewBox="0 0 12 12" aria-hidden="true"><rect x="1" y="2.5" width="10" height="7" fill="currentColor"/><path d="M1 2.5l5 4 5-4" stroke="var(--brand-blue)" fill="none"/></svg>l.brenner@nordlicht-pb.de</li>
        <li><svg viewBox="0 0 12 12" aria-hidden="true"><circle cx="6" cy="6" r="5" fill="currentColor"/><path d="M1 6h10M6 1c-2 3-2 7 0 10M6 1c2 3 2 7 0 10" stroke="var(--brand-blue)" fill="none" stroke-width="0.8"/></svg>www.nordlicht-pb.de</li>
      </ul>
    </div>
  </section>

  <section class="card card-back" aria-label="Rückseite">
    <div class="back-accent" aria-hidden="true"></div>
    <div class="back-logo">
      <span class="logo-square"></span>
      <span class="logo-text">NORDLICHT<span class="logo-sub">PERSONALBERATUNG</span></span>
    </div>
  </section>
</body>
</html>
```